Business Card Design Project

Looking to update our business cards. We have a logo with our slogan. We are an IT firm so we wouldlike a modern look.

Industry/Entity Type

Business

```html
<!DOCTYPE html>
<html lang="en">
<head>
<meta charset="utf-8">
<title>Nexbyte Inc — Business Card Set</title>
<link rel="stylesheet" href="https://fonts.googleapis.com/css2?family=Jost:ital,wght@0,400;0,500;0,600;0,700;1,700&display=swap">
<style>
  :root {
    --stage: #e9e6e1;
    --label: #1a1a1a;
    --brand-green: #6a833a;
    --lime: #b3cc3a;
    --steel-mid: #5a5a5a;
    --ink: #2b2b2b;
    --white: #ffffff;
    --navy: #1e2a4a;
  }
  * { box-sizing: border-box; margin: 0; padding: 0; }
  html, body { width: 1200px; height: 788px; overflow: hidden; }
  body { background: var(--stage); position: relative; font-family: "Jost", sans-serif; }

  .variant-label {
    position: absolute; width: 524px; text-align: center;
    font: 400 22px "Jost", sans-serif; color: var(--label);
  }

  .card {
    position: absolute; width: 524px; height: 299px;
    border-radius: 22px; overflow: hidden;
    box-shadow: 0 3px 8px rgba(0,0,0,.25);
  }
  .card-front { left: 52px; top: 82px; }
  .card-back-white { left: 621px; top: 80px; background: var(--white); }
  .card-back-steel { left: 49px; top: 455px;
    background: linear-gradient(135deg, var(--steel-mid) 0%, #3a3a3a 45%, #141414 100%); }
  .card-back-glow { left: 621px; top: 455px; }

  .card-art { position: absolute; inset: 0; width: 100%; height: 100%; }

  .glow-backdrop {
    position: absolute; inset: 0;
    background:
      radial-gradient(ellipse 45% 55% at 52% 55%, #ffffff 0%, #cfe0ff 25%, rgba(90,130,230,.6) 55%, transparent 80%),
      linear-gradient(180deg, #3348b8 0%, #2a63d8 45%, #1b2f90 100%);
  }

  .brand { position: absolute; text-align: center; }
  .brand-name {
    font: 600 52px/1 "Jost", sans-serif; letter-spacing: 6px;
    color: var(--brand-green); display: flex; align-items: center; justify-content: center; gap: 12px;
  }
  .brand-dot { width: 14px; height: 14px; border-radius: 50%; background: var(--brand-green); }
  .brand-slogan {
    font: 700 13px/1 "Jost", sans-serif; letter-spacing: 3.6px;
    color: var(--ink); margin-top: 8px; text-transform: uppercase;
  }

  .card-front .brand { left: 26px; top: 52px; text-align: left; }
  .card-front .brand-name { color: var(--white); font-size: 40px; justify-content: flex-start; }
  .card-front .brand-dot { background: var(--white); width: 11px; height: 11px; }
  .card-front .brand-slogan { color: #1f2a12; font-size: 10.5px; letter-spacing: 2.6px; margin-top: 6px; }

  .centered { left: 0; right: 0; top: 118px; }
  .card-back-steel .brand-slogan { color: #1b1b1b; }
  .card-back-glow .brand-slogan { color: var(--navy); }

  .contact { position: absolute; right: 26px; text-align: right; color: var(--white); }
  .contact-name { top: 88px; }
  .person-name { font: 600 18px "Jost", sans-serif; }
  .person-role { font: 400 13px "Jost", sans-serif; margin-top: 0; }
  .contact-phone { top: 160px; font-size: 13.5px; }
  .contact-web { top: 191px; font-size: 13px; line-height: 17px; }
  .contact-address { top: 257px; font-size: 13px; }
  .key { font-weight: 700; font-style: italic; }
</style>
</head>
<body>

  <div class="variant-label" style="left:58px; top:34px;">Front</div>
  <div class="variant-label" style="left:635px; top:34px;">Back - 1</div>
  <div class="variant-label" style="left:58px; top:404px;">Back - 2</div>
  <div class="variant-label" style="left:635px; top:404px;">Back - 3</div>

  <section class="card card-front">
    <svg class="card-art" viewBox="0 0 524 299" aria-hidden="true">
      <defs>
        <linearGradient id="steel" x1="0" y1="0" x2="0" y2="1">
          <stop offset="0" stop-color="#9a9a9a"/>
          <stop offset=".45" stop-color="#6a6a6a"/>
          <stop offset="1" stop-color="#1e1e1e"/>
        </linearGradient>
      </defs>
      <rect width="524" height="299" fill="url(#steel)"/>
      <path d="M0 0 H524 V8 C390 40 200 120 28 299 H0 Z" fill="#6a833a"/>
      <path d="M524 18 C380 60 210 145 42 299" fill="none" stroke="#b3cc3a" stroke-width="9"/>
    </svg>
    <div class="brand">
      <div class="brand-name">NEXBYTE<span class="brand-dot"></span></div>
      <div class="brand-slogan">Making Technology Easy</div>
    </div>
    <div class="contact contact-name">
      <div class="person-name">Your Name</div>
      <div class="person-role">Designation</div>
    </div>
    <div class="contact contact-phone"><span class="key">p</span> : +12 345 6789</div>
    <div class="contact contact-web">
      <div><span class="key">e</span> : info@website.com</div>
      <div><span class="key">w</span> : www.website.com</div>
    </div>
    <div class="contact contact-address">#0000, Street Name, Area Name, Country Code</div>
  </section>

  <section class="card card-back-white">
    <div class="brand centered">
      <div class="brand-name">NEXBYTE<span class="brand-dot"></span></div>
      <div class="brand-slogan">Making Technology Easy</div>
    </div>
  </section>

  <section class="card card-back-steel">
    <div class="brand centered">
      <div class="brand-name">NEXBYTE<span class="brand-dot"></span></div>
      <div class="brand-slogan">Making Technology Easy</div>
    </div>
  </section>

  <section class="card card-back-glow">
    <div class="glow-backdrop" role="img" aria-label="Abstract blue technology backdrop with a bright central light burst, digital rings and binary streaks"></div>
    <div class="brand centered">
      <div class="brand-name">NEXBYTE<span class="brand-dot"></span></div>
      <div class="brand-slogan">Making Technology Easy</div>
    </div>
  </section>

</body>
</html>
```